Business card design

We need a business card designed completed for a new company. We are a company that works with associations, schools to convert their older text/DVDs into dynamic online and mobile programs. Our initial platform is designed for the legal associations and will enable their lawyers to access their content such as forms, videos, case law and support materials anywhere, anytime. We are also focused on Project Management Associations, Financial Management Associations and IT Associations.

I would like for the business card to have the following information:

Logo

Kent marrowby

President and CEO

kmarrowby@trevantiq.example

Mobile: 555-374-9160

www.trevantiq.example

Tag line: Transforming content into a mobile platform    

I would like it to be double sided, use the colours of the logo, tie into the mobile world

 

Industry/Entity Type

Legal

Logo Text

Trevantiq

```html
<!DOCTYPE html>
<html lang="en">
<head>
<meta charset="utf-8">
<title>Trevantiq business card set</title>
<link rel="stylesheet" href="https://fonts.googleapis.com/css2?family=Open+Sans:wght@400;600;700;800&display=swap">
<style>
  :root {
    --backdrop: #7a5638;
    --label: #1c140e;
    --card-grey: #9a9a9a;
    --card-white: #ffffff;
    --band: #6a6a6a;
    --rule-light: #f2f2f2;
    --rule-dark: #8a8a8a;
    --ink-light: #ffffff;
    --ink-dark: #1a1a1a;
    --logo-on-white: #555555;
  }
  * { box-sizing: border-box; margin: 0; padding: 0; }
  html, body { width: 1200px; height: 800px; overflow: hidden; }
  body {
    position: relative;
    background: var(--backdrop);
    font-family: "Open Sans", Arial, sans-serif;
  }
  .view-label {
    position: absolute;
    width: 510px;
    text-align: center;
    font-size: 21px;
    color: var(--label);
  }
  .card {
    position: absolute;
    width: 510px;
    height: 290px;
    border-radius: 22px;
    overflow: hidden;
  }
  .card--grey { background: var(--card-grey); }
  .card--white { background: var(--card-white); }
  .wordmark {
    position: absolute;
    left: 0; right: 0;
    text-align: center;
    font-weight: 800;
    letter-spacing: -1px;
    line-height: 1;
  }
  .card--grey .wordmark { color: var(--ink-light); }
  .card--white .wordmark { color: var(--logo-on-white); }
  .wordmark--top { top: 58px; font-size: 66px; }
  .wordmark--center { top: 98px; font-size: 78px; }
  .rule {
    position: absolute;
    left: 0; right: 0;
    height: 2px;
  }
  .card--grey .rule { background: var(--rule-light); }
  .card--white .rule { background: var(--rule-dark); }
  .rule--upper { top: 168px; }
  .rule--lower { top: 239px; }
  .band {
    position: absolute;
    left: 0; right: 0;
    top: 173px;
    height: 63px;
    background: var(--band);
    color: var(--ink-light);
  }
  .identity { position: absolute; left: 48px; top: 13px; }
  .identity__name { font-size: 16px; font-weight: 700; line-height: 20px; }
  .identity__title { font-size: 12.5px; line-height: 18px; }
  .tagline {
    position: absolute;
    right: 48px; top: 11px;
    text-align: right;
    font-size: 15px;
    line-height: 20px;
  }
  .contact {
    position: absolute;
    left: 0; right: 0;
    top: 253px;
    text-align: center;
    font-size: 12.5px;
  }
  .card--grey .contact { color: var(--ink-dark); }
  .card--white .contact { color: var(--ink-dark); }
  .contact b { font-weight: 700; font-style: italic; }
  .web-address {
    position: absolute;
    left: 0; right: 0;
    top: 252px;
    text-align: center;
    font-size: 16px;
    letter-spacing: 3px;
    color: var(--ink-dark);
  }
</style>
</head>
<body>
  <div class="view-label" style="left:72px; top:50px;">Front</div>
  <div class="view-label" style="left:631px; top:50px;">Back - 1</div>
  <div class="view-label" style="left:72px; top:410px;">Back - 2</div>
  <div class="view-label" style="left:633px; top:410px;">Back - 3</div>

  <section class="card card--grey" style="left:72px; top:90px;">
    <div class="wordmark wordmark--top">Trevantiq</div>
    <div class="rule rule--upper"></div>
    <div class="band">
      <div class="identity">
        <div class="identity__name">Kent marrowby</div>
        <div class="identity__title">President and CEO</div>
      </div>
      <div class="tagline">Transforming content<br>into a mobile platform</div>
    </div>
    <div class="rule rule--lower"></div>
    <div class="contact"><b>C</b> : 555-374-9160 &nbsp;| &nbsp;<b>E</b> : kmarrowby@trevantiq.example &nbsp;| &nbsp;<b>W</b> : www.trevantiq.example</div>
  </section>

  <section class="card card--white" style="left:631px; top:90px;">
    <div class="wordmark wordmark--top">Trevantiq</div>
    <div class="rule rule--upper"></div>
    <div class="band">
      <div class="identity">
        <div class="identity__name">Kent marrowby</div>
        <div class="identity__title">President and CEO</div>
      </div>
      <div class="tagline">Transforming content<br>into a mobile platform</div>
    </div>
    <div class="rule rule--lower"></div>
    <div class="contact"><b>C</b> : 555-374-9160 &nbsp;| &nbsp;<b>E</b> : kmarrowby@trevantiq.example &nbsp;| &nbsp;<b>W</b> : www.trevantiq.example</div>
  </section>

  <section class="card card--grey" style="left:72px; top:452px;">
    <div class="wordmark wordmark--center">Trevantiq</div>
    <div class="web-address">www.trevantiq.example</div>
  </section>

  <section class="card card--white" style="left:633px; top:450px;">
    <div class="wordmark wordmark--center">Trevantiq</div>
    <div class="web-address">www.trevantiq.example</div>
  </section>
</body>
</html>
```